Product Label Redesign for a CBD Balm - 7.25" x 1.5"

We are redesigning our product label for a CBD balm to comply with federal standards and copyright issues. We are looking for designs that stand out on a shelf, but also have a professional look to them. Base color is flat black, with bright greens that pop out. Other colors are optional. We want to impart quality, but not look boring or medicinal. Attached is our current label (Harlow's Pick) and the sample label we used as a guide (Vireo Leaf). Please design a label that would stand out among a shelf of various CBD balms. For more information PLEASE VISIT our website at https://harlowspick.example/.
Label dimensions are 7.25" x 1.5"
Thank you! - Gregory

Target Market(s)

General public.

Industry/Entity Type

CND balms and lotions.

Font styles to use
Sans Serif

Requirements
Must have
• ALL the content of the current label plus bar code. Size: 7.25" x 1.5"
Nice to have
• A design that really stands out on a shelf of CBD products. We are currently using flat black and bright green, but are open to other colors.
Should not have
• By law we cannot use the works "pain" or "relief" or any other similar words. We DO NOT want any association with marijuana as our product does not contain it--only CBD. So please no pot leaves.

```html
<!DOCTYPE html>
<html lang="en">
<head>
<meta charset="utf-8">
<title>Harlow's Pick CBD Muscle and Joint Balm Label</title>
<link href="https://fonts.googleapis.com/css2?family=Poppins:wght@400;500;600;700;800&display=swap" rel="stylesheet">
<style>
  :root {
    --page: #ffffff;
    --label-black: #121212;
    --label-black-soft: #1a1a1a;
    --green: #8cc63f;
    --green-bright: #9fd61c;
    --green-deep: #4f8a10;
    --orange: #e8673a;
    --white: #ffffff;
    --grey: #d6d6d6;
  }
  * { box-sizing: border-box; margin: 0; padding: 0; }
  html, body {
    width: 1063px; height: 1200px; overflow: hidden;
    background: var(--page);
    font-family: "Poppins", sans-serif;
  }
  .label {
    position: absolute; left: 30px; top: 497px;
    width: 1003px; height: 207px;
    background: radial-gradient(ellipse at 55% 40%, var(--label-black-soft), var(--label-black) 70%);
    color: var(--white);
    overflow: hidden;
  }
  .label__band {
    position: absolute; left: 0; bottom: 0; width: 100%; height: 12px;
    background: linear-gradient(90deg, var(--green-deep), var(--green-bright) 40%, var(--green-bright));
  }
  .brand { position: absolute; display: flex; align-items: center; font-weight: 600; }
  .brand__mark { width: 20px; height: 20px; background: var(--orange); margin-right: 9px; }
  .brand--side { left: 19px; top: 18px; font-size: 14px; }
  .brand--center {
    left: 0; width: 1003px; top: 16px; flex-direction: column;
    font-size: 8.5px;
  }
  .brand--center .brand__mark { width: 16px; height: 16px; margin: 0 0 4px; }

  .info { position: absolute; font-size: 9.4px; line-height: 1.17; }
  .info--visit { left: 19px; top: 60px; width: 150px; text-align: justify; }
  .site-link { position: absolute; left: 19px; top: 104px; font-size: 11.6px; font-weight: 800; color: var(--green-bright); letter-spacing: 0.2px; }
  .info--warning { left: 19px; top: 129px; width: 146px; }
  .accent { color: var(--green-bright); }
  .child-warning {
    position: absolute; left: 19px; top: 173px; width: 141px; height: 13px;
    background: var(--orange); font-size: 7.2px; font-weight: 600;
    display: flex; align-items: center; padding-left: 6px;
  }
  .info--directions { left: 176px; top: 15px; width: 160px; }
  .info--active { left: 176px; top: 80px; width: 160px; }
  .info--inactive { left: 176px; top: 126px; width: 150px; }

  .hero { position: absolute; left: 0; width: 1003px; text-align: center; }
  .hero__natural { top: 59px; font-size: 6px; letter-spacing: 4.6px; font-weight: 500; }
  .hero__cbd {
    top: 66px; font-size: 56px; font-weight: 800; color: var(--green-bright);
    line-height: 1; letter-spacing: -1px;
  }
  .hero__frame { position: absolute; left: 405px; top: 95px; width: 193px; height: 56px; }
  .hero__title { top: 120px; font-size: 13.4px; font-weight: 700; color: var(--grey); }
  .hero__pure { top: 138px; font-size: 5.4px; letter-spacing: 4.6px; color: var(--grey); }
  .hero__origin { top: 166px; font-size: 5.6px; letter-spacing: 6px; font-weight: 600; }
  .hero__specs {
    top: 178px; display: flex; justify-content: center; gap: 9px;
    font-size: 5.6px; font-weight: 700; align-items: center;
  }
  .hero__divider { width: 1px; height: 10px; background: var(--white); }

  .benefits { position: absolute; left: 670px; top: 62px; list-style: none; font-size: 10.2px; line-height: 1.15; }
  .benefits li { display: flex; align-items: flex-start; margin-bottom: 10px; }
  .benefits svg { flex: none; width: 10px; height: 10px; margin: 1px 7px 0 0; }

  .code-panel { position: absolute; left: 892px; top: 16px; width: 68px; height: 168px; background: var(--white); }
</style>
</head>
<body>
  <section class="label">
    <div class="brand brand--side"><span class="brand__mark"></span>Harlow's Pick</div>
    <p class="info info--visit">To view our other products or repurchase, visit our website at www.harlowspick.example.</p>
    <p class="site-link">HARLOWSPICK.EXAMPLE</p>
    <p class="info info--warning"><span class="accent">Warning:</span> For external use only. Use only as directed. Keep away from eyes.</p>
    <p class="child-warning">KEEP OUT OF REACH OF CHILDREN.</p>

    <p class="info info--directions"><span class="accent">Directions:</span> Rub in a small amount over the affected area 3-4 times daily.</p>
    <p class="info info--active"><span class="accent">Active Ingradients:</span><br>Menthol 6%</p>
    <p class="info info--inactive"><span class="accent">Inactive Ingradients:</span> Bees wax, Olive oil, camphor, CBD hemp extract, CBN hemp extract, eucalyptus oil, clove oil, peppermint oil, tea tree oil, sorbic acid.</p>

    <div class="brand brand--center"><span class="brand__mark"></span>Harlow's Pick</div>
    <svg class="hero__frame" viewBox="0 0 193 56" aria-hidden="true">
      <path d="M38 0.5 H0.5 V55.5 H192.5 V0.5 H155" fill="none" stroke="var(--green)" stroke-width="1"/>
    </svg>
    <p class="hero hero__natural">100% NATURAL</p>
    <p class="hero hero__cbd">CBD</p>
    <p class="hero hero__title">MUSCLE AND JOINT BALM</p>
    <p class="hero hero__pure">PURE CBD</p>
    <p class="hero hero__origin">MADE IN SONOMA CA</p>
    <div class="hero hero__specs"><span>500MG</span><span class="hero__divider"></span><span>4 FL OZ</span><span class="hero__divider"></span><span>118ML</span></div>

    <ul class="benefits">
      <li><svg viewBox="0 0 10 10"><circle cx="5" cy="5" r="5" fill="var(--orange)"/><path d="M2.6 5.1 L4.3 6.7 L7.4 3.5" fill="none" stroke="#fff" stroke-width="1.3"/></svg><span>Long - lasting comfort for neck, back<br>and tired muscles, including joints</span></li>
      <li><svg viewBox="0 0 10 10"><circle cx="5" cy="5" r="5" fill="var(--orange)"/><path d="M2.6 5.1 L4.3 6.7 L7.4 3.5" fill="none" stroke="#fff" stroke-width="1.3"/></svg><span>Made from all natural ingredients.</span></li>
      <li><svg viewBox="0 0 10 10"><circle cx="5" cy="5" r="5" fill="var(--orange)"/><path d="M2.6 5.1 L4.3 6.7 L7.4 3.5" fill="none" stroke="#fff" stroke-width="1.3"/></svg><span>Moisturizes skin while soothing muscles</span></li>
    </ul>

    <div class="code-panel"></div>
    <div class="label__band"></div>
  </section>
</body>
</html>
```